Lantern Petals Website v.1 - attract floral shop franchisees

I need a simple information website for my new business. We are a franchisor of flower shops. The overall purpose of the website is to promote the company and the service, especially to potential franchisees and retailers. Only about 4 pages are required including homepage, About, For Supermarkets, For Franchisees, and Contact. No special functions are required except the site will have two separate inquiry forms that must be filled out online and submitted via automated email. Similarly, an email form should be linked from the Contact page. I have a logo and business cards designed by ArtMingle, and I would like the site to have a consistent color scheme and style. The key to design will be to express the joy and love associated with flowers and floral bouquets.
IMPORTANT - I will be exporting the website design to Wordpress CMS in a site hosted by HostNimbus. For smooth integration into WordPress hosted by HostNimbus, the designer should build the site using a WordPress-friendly format. Ideally, they should use HTML, CSS, and PHP. Creating a custom theme or using a page builder that exports to WordPress-compatible files is best. This ensures the site can be easily imported and managed within WordPress.

Target Market(s)

Potential franchisees (existing florists or creative types who might like to own a floral business) and supermarkets who might want us to run their floral department

Industry/Entity Type

Floral retailing

Requirements
Must have
• A brand theme that is beautiful, consistent throughout and builds on the logo design
Nice to have
• Show gender and ethnic diversity in customers and florists. Pictures of happy florists (for franchisees) and pictures of amazing floral department displays (for supermarkets)

```html
<!DOCTYPE html>
<html lang="en">
<head>
<meta charset="utf-8">
<title>Lantern Petals – Freshest Flowers, Artisan Designs, Franchise Opportunities</title>
<link href="https://fonts.googleapis.com/css2?family=Oswald:wght@400;500&family=Quicksand:wght@400;500;600;700&family=Yellowtail&display=swap" rel="stylesheet">
<style>
:root{
  --green:#0b8a3a;
  --green-dark:#087530;
  --orange:#f29a00;
  --ink:#1d1d1d;
  --text:#3c3c3c;
  --grey-band:#efefef;
  --cream:#fcf6e8;
  --white:#ffffff;
  --line:#d9d9d9;
  --photo-warm:#c9b8a4;
  --photo-flora:#b86a5a;
  --photo-green:#5d7a4a;
  --dark-field:#2b3326;
}
*{box-sizing:border-box;margin:0;padding:0}
html,body{width:1200px;height:3388px;overflow:hidden}
body{position:relative;background:var(--white);font-family:"Quicksand",sans-serif;color:var(--text)}
.abs{position:absolute}
.script{font-family:"Yellowtail",cursive;font-weight:400}
.photo{position:absolute}

/* header */
.site-header{position:absolute;left:0;top:0;width:1200px;height:110px;background:var(--white)}
.brand{position:absolute;left:141px;top:30px;display:flex;align-items:center;gap:12px}
.brand-dot{width:40px;height:40px;border-radius:50%;background:var(--orange)}
.brand-name{font-family:"Quicksand",sans-serif;font-weight:700;font-size:28px;color:var(--green)}
.contact-bar{position:absolute;right:141px;top:8px;display:flex;gap:26px;font-size:14px;font-weight:500;color:var(--ink)}
.contact-bar span{display:flex;align-items:center;gap:12px}
.ic{width:32px;height:32px;border-radius:50%;background:#fdeccc;display:flex;align-items:center;justify-content:center}
.header-rule{position:absolute;left:450px;right:141px;top:58px;border-top:1px solid var(--line)}
.main-nav{position:absolute;left:505px;top:76px;display:flex;gap:50px;font-size:13px;font-weight:600;color:var(--ink)}
.main-nav .active{color:var(--orange)}

/* hero */
.hero{position:absolute;left:0;top:110px;width:1200px;height:530px;background:linear-gradient(100deg,#6b5f55 0%,#8f8076 35%,#c8beb5 62%,#e2dbd3 100%)}
.hero-title{position:absolute;left:141px;top:135px;font-family:"Oswald",sans-serif;font-weight:500;font-size:58px;line-height:66px;color:var(--white);letter-spacing:-0.5px}
.btn{position:absolute;background:var(--orange);color:var(--ink);font-weight:600;font-size:14px;display:flex;align-items:center;justify-content:center}
.hero .btn{left:141px;top:344px;width:127px;height:42px}

/* about */
.section-title{font-family:"Yellowtail",cursive;font-size:50px;color:var(--ink);line-height:1}
.section-title em{font-style:normal;color:var(--orange)}
.divider{display:flex;align-items:center;gap:8px}
.divider i{display:block;width:42px;border-top:2px solid var(--green)}
.divider b{width:14px;height:14px;border-radius:50%;background:var(--green)}
.about-copy{position:absolute;left:650px;top:855px;width:405px;font-size:12.5px;line-height:23px;font-weight:500}
.about-copy p+p{margin-top:8px}

/* band */
.grey-band{position:absolute;left:0;top:1285px;width:1200px;height:460px;background:var(--grey-band)}
.band-copy{position:absolute;left:141px;top:1397px;width:445px;font-size:12.5px;line-height:23px;font-weight:500}
.band-copy p+p{margin-top:7px}
.arch-frame{position:absolute;left:668px;top:1357px;width:382px;height:495px;background:var(--white);border-radius:191px 191px 0 0;box-shadow:0 2px 12px rgba(0,0,0,.06)}
.arrow{position:absolute;width:46px;height:46px;border-radius:50%;display:flex;align-items:center;justify-content:center}
.arrow.outline{border:2px solid var(--green);background:var(--white)}
.arrow.filled{background:var(--green)}

/* gallery */
.dark-field{position:absolute;left:0;top:2117px;width:1200px;height:401px;background:linear-gradient(180deg,#3a4431,var(--dark-field))}
.tile{position:absolute;top:1917px;width:214px;height:270px;border:3px solid var(--white)}
.partner-name{position:absolute;left:0;width:1200px;top:2316px;text-align:center;color:var(--white);font-weight:700;font-size:16px;letter-spacing:6px}
.partner-copy{position:absolute;left:150px;width:900px;top:2386px;text-align:center;color:var(--white);font-size:12.5px;line-height:23px;font-weight:500}

/* testimonials */
.review-card{position:absolute;left:217px;top:2740px;width:766px;height:210px;background:var(--cream);border-radius:22px}
.reviewer{position:absolute;left:0;width:1200px;top:2800px;text-align:center;font-family:"Yellowtail",cursive;font-size:20px;color:var(--ink)}
.reviewer em{font-style:normal;color:var(--orange)}
.review-text{position:absolute;left:355px;width:490px;top:2843px;text-align:center;font-size:12.5px;line-height:23px;font-weight:500}
.stars{position:absolute;left:0;width:1200px;top:2902px;text-align:center;color:var(--orange);font-size:15px;letter-spacing:3px}

/* footer */
.site-footer{position:absolute;left:0;top:3034px;width:1200px;height:354px;background:var(--green);color:var(--white)}
.foot-title{font-family:"Yellowtail",cursive;font-size:20px}
.foot-div{display:flex;align-items:center;gap:6px;margin-top:4px}
.foot-div i{display:block;width:20px;border-top:1px solid var(--white)}
.foot-div b{width:8px;height:8px;border-radius:50%;background:var(--white)}
.quick-links{position:absolute;left:141px;top:60px}
.quick-links ul{list-style:none;margin-top:22px;font-size:12px;font-weight:500}
.quick-links li{height:33px}
.foot-brand{position:absolute;left:430px;top:125px;display:flex;align-items:center;gap:14px}
.foot-brand .brand-dot{width:64px;height:64px}
.foot-brand .brand-name{font-size:40px;color:var(--white)}
.social{position:absolute;left:482px;top:222px;display:flex;gap:6px}
.social i{width:29px;height:29px;border-radius:50%;border:1.5px solid var(--white);display:block}
.contact-details{position:absolute;left:853px;top:60px}
.contact-details ul{list-style:none;margin-top:26px;font-size:12px;font-weight:500;line-height:18px}
.contact-details li{display:flex;align-items:center;gap:12px;margin-bottom:20px}
.contact-details .ic{width:36px;height:36px;background:var(--orange);flex:none}
.foot-rule{position:absolute;left:141px;right:141px;top:3345px;border-top:1px solid rgba(255,255,255,.3)}
.copyright{position:absolute;left:0;width:1200px;top:3356px;text-align:center;font-size:12px;color:var(--white)}
</style>
</head>
<body>

<header class="site-header">
  <div class="brand"><span class="brand-dot"></span><span class="brand-name">Lantern Petals</span></div>
  <div class="contact-bar">
    <span><span class="ic"><svg width="14" height="14" viewBox="0 0 24 24"><path fill="#0b8a3a" d="M6.6 10.8a15 15 0 0 0 6.6 6.6l2.2-2.2c.3-.3.7-.4 1-.2 1.1.4 2.3.6 3.6.6.6 0 1 .4 1 1V20c0 .6-.4 1-1 1A17 17 0 0 1 3 4c0-.6.4-1 1-1h3.5c.6 0 1 .4 1 1 0 1.3.2 2.5.6 3.6.1.3 0 .7-.2 1z"/></svg></span>123-456-7890</span>
    <span><span class="ic"><svg width="14" height="12" viewBox="0 0 24 18"><rect x="1" y="1" width="22" height="16" rx="2" fill="#0b8a3a"/><path d="M2 2l10 8 10-8" stroke="#fff" stroke-width="2" fill="none"/></svg></span>info@lanternpetals.com</span>
  </div>
  <div class="header-rule"></div>
  <nav class="main-nav"><span class="active">Home</span><span>About Us</span><span>For Supermarkets</span><span>For Franchisees</span></nav>
</header>

<section class="hero" role="img" aria-label="Smiling florist arranging red and white roses in a flower shop">
  <h1 class="hero-title">Freshest Flowers<br>Artisan Designs<br>Franchise Opportunities</h1>
  <span class="btn">Contact Us</span>
</section>

<!-- about -->
<div class="photo" role="img" aria-label="Florist standing with bouquets of roses and hydrangeas" style="left:143px;top:785px;width:245px;height:315px;border-radius:120px 0 0 120px / 120px 0 0 120px;border-top-left-radius:0;border-top-right-radius:0;border-radius:0 0 0 110px;background:linear-gradient(160deg,#a8b49a,#d9c35a 55%,#9fb3c8)"></div>
<div class="photo" role="img" aria-label="Vases of orange and yellow protea arrangements" style="left:410px;top:735px;width:175px;height:222px;border-radius:90px 0 90px 0;background:linear-gradient(150deg,#6a5b40,#d9901f 55%,#3f3a2c)"></div>
<div class="photo" role="img" aria-label="Glass vases filled with pink mixed bouquets" style="left:410px;top:979px;width:175px;height:222px;border-radius:90px 0 90px 0;background:linear-gradient(150deg,#5a4032,#c86d8a 55%,#7a5a3d)"></div>
<div class="abs" style="left:650px;top:756px">
  <h2 class="section-title">About <em>Us</em></h2>
  <div class="divider" style="margin-top:10px"><i></i><b></b><i></i></div>
</div>
<div class="about-copy">
  <p>Fresh flowers convey beauty and love, and in our view should become something every person regularly enjoys. Lantern Petals is an entrepreneurial company created to make top quality fresh flowers and professionally-designed bouquets accessible to every consumer at affordable prices.</p>
  <p>Professional florists typically sell the finest quality stems, design the most beautiful bouquets and provide the finest customer service, but their costs – of floral products, retail spaces, labor and marketing – force them to pass high prices along to customers. Supermarket flower departments benefit from high customer footfall, economies of scale and low pricing, but their quality of stems and bouquets is typically poor, staffing is limited, and staff turnover is high which can result in inefficiency, wastage, poorly merchandised selections and limited service.</p>
</div>
<div class="photo" role="img" aria-label="Line drawing of tulip stems" style="left:990px;top:990px;width:210px;height:280px;background:linear-gradient(160deg,rgba(143,160,170,.18),rgba(143,160,170,.05))"></div>

<!-- band -->
<div class="grey-band"></div>
<div class="band-copy">
  <p>Lantern Petals brings the best of professional florists and supermarkets together for the benefit of consumers. It supports a national network of owner-operator franchisees, who in many cases are multi-site professional florists, with comprehensive services to enhance franchise profitability. Lantern Petals works with some of the country's largest and most progressive supermarkets to provide franchisee ownership and operation of their strategically important floral departments.</p>
  <p>Supermarkets find that Lantern Petals is able to improve their financial outcomes, provide attentive customer service and satisfaction, and lift the quality of the entire store environment.</p>
</div>
<div class="photo" role="img" aria-label="Line drawing of blossoms" style="left:18px;top:1592px;width:104px;height:138px;background:linear-gradient(160deg,rgba(80,100,120,.14),rgba(80,100,120,.04))"></div>
<div class="arch-frame"></div>
<div class="photo" role="img" aria-label="Florist trimming roses at a workbench" style="left:678px;top:1370px;width:362px;height:460px;border-radius:181px 181px 0 0;background:linear-gradient(170deg,#5a4634,#8a7560 45%,#b88a8f 75%,#6a4f3a)"></div>
<span class="arrow outline" style="left:542px;top:1767px"><svg width="12" height="12" viewBox="0 0 12 12"><path d="M8 2L4 6l4 4" stroke="#1d1d1d" stroke-width="2" fill="none"/></svg></span>
<span class="arrow filled" style="left:602px;top:1767px"><svg width="12" height="12" viewBox="0 0 12 12"><path d="M4 2l4 4-4 4" stroke="#fff" stroke-width="2" fill="none"/></svg></span>

<!-- gallery -->
<div class="dark-field" role="img" aria-label="Field of red gerbera flowers in a greenhouse"></div>
<div class="tile photo" role="img" aria-label="Display of roses and hydrangeas" style="left:141px;border-radius:40px 0 40px 0;background:linear-gradient(160deg,#cfcac2,#b8416a 55%,#5d7a4a)"></div>
<div class="tile photo" role="img" aria-label="Florist selecting flowers from buckets" style="left:377px;top:1947px;border-radius:40px 0 40px 0;background:linear-gradient(160deg,#d9d2cc,#c8545a 55%,#7a8a5a)"></div>
<div class="tile photo" role="img" aria-label="Flower shop storefront with potted plants" style="left:612px;border-radius:0 0 40px 0;background:linear-gradient(160deg,#4a5a4a,#b08a86 55%,#5d6a55)"></div>
<div class="tile photo" role="img" aria-label="Florist in apron behind white roses" style="left:846px;top:1947px;border-radius:40px 0 40px 0;background:linear-gradient(160deg,#e5e2dc,#a0303a 55%,#ece6dc)"></div>
<div class="partner-name">FROSTLINE GROUP</div>
<p class="partner-copy">Lantern Petals operates in partnership with Frostline Group, the leading franchisor of sushi stations and pre-packaged fruit &amp; vegetable departments to supermarkets across the United States and United Kingdom. Lantern Petals' combination of floral and supermarket franchising expertise guarantees that consumers, franchisees and supermarket partners each receive exceptional service and value.</p>

<!-- testimonials -->
<div class="abs" style="left:0;width:1200px;top:2600px;display:flex;flex-direction:column;align-items:center">
  <h2 class="section-title">What Our Customers <em>Say</em></h2>
  <div class="divider" style="margin-top:12px"><i></i><b></b><i></i></div>
</div>
<div class="review-card"></div>
<div class="photo" role="img" aria-label="Line drawing of a flowering branch" style="left:240px;top:2795px;width:92px;height:130px;background:linear-gradient(160deg,rgba(40,60,80,.12),rgba(40,60,80,.03))"></div>
<div class="photo" role="img" aria-label="Line drawing of a leafy sprig" style="left:862px;top:2788px;width:105px;height:150px;background:linear-gradient(160deg,rgba(40,60,80,.12),rgba(40,60,80,.03))"></div>
<div class="photo" role="img" aria-label="Customer portrait" style="left:564px;top:2706px;width:72px;height:72px;border-radius:50%;background:linear-gradient(160deg,#b06a55,#5aa6c8)"></div>
<div class="reviewer">Mira <em>Hollis</em></div>
<p class="review-text">Lorem ipsum dolor sit amet, consectetur adipiscing elit, sed do eiusmod tempor incididunt ut labore et dolore magna aliqua.</p>
<div class="stars">★★★★★</div>
<span class="arrow outline" style="left:157px;top:2826px;width:36px;height:36px"><svg width="10" height="10" viewBox="0 0 12 12"><path d="M8 2L4 6l4 4" stroke="#1d1d1d" stroke-width="2" fill="none"/></svg></span>
<span class="arrow filled" style="left:1007px;top:2826px;width:36px;height:36px"><svg width="10" height="10" viewBox="0 0 12 12"><path d="M4 2l4 4-4 4" stroke="#fff" stroke-width="2" fill="none"/></svg></span>

<!-- footer -->
<footer class="site-footer">
  <div class="quick-links">
    <div class="foot-title">Quick Links</div>
    <div class="foot-div"><i></i><b></b><i></i></div>
    <ul><li>Home</li><li>About Us</li><li>For Supermarkets</li><li>For Franchisees</li><li>Contact Us</li></ul>
  </div>
  <div class="foot-brand"><span class="brand-dot"></span><span class="brand-name">Lantern Petals</span></div>
  <div class="social"><i></i><i></i><i></i><i></i></div>
  <div class="contact-details">
    <div class="foot-title">Contact Details</div>
    <div class="foot-div"><i></i><b></b><i></i></div>
    <ul>
      <li><span class="ic"><svg width="14" height="18" viewBox="0 0 14 18"><path d="M7 0a7 7 0 0 0-7 7c0 5 7 11 7 11s7-6 7-11a7 7 0 0 0-7-7z" fill="#fff"/><circle cx="7" cy="7" r="2.5" fill="#f29a00"/></svg></span><span>123, Building Name, Street<br>City, State XY 123456</span></li>
      <li><span class="ic"><svg width="14" height="14" viewBox="0 0 24 24"><path fill="#fff" d="M6.6 10.8a15 15 0 0 0 6.6 6.6l2.2-2.2c.3-.3.7-.4 1-.2 1.1.4 2.3.6 3.6.6.6 0 1 .4 1 1V20c0 .6-.4 1-1 1A17 17 0 0 1 3 4c0-.6.4-1 1-1h3.5c.6 0 1 .4 1 1 0 1.3.2 2.5.6 3.6.1.3 0 .7-.2 1z"/></svg></span><span>123-456-7890</span></li>
      <li><span class="ic"><svg width="14" height="11" viewBox="0 0 24 18"><rect x="1" y="1" width="22" height="16" rx="2" fill="#fff"/><path d="M2 2l10 8 10-8" stroke="#f29a00" stroke-width="2" fill="none"/></svg></span><span>info@lanternpetals.com</span></li>
    </ul>
  </div>
</footer>
<div class="foot-rule"></div>
<div class="copyright">©2024 Lantern Petals. All Rights Reserved.</div>

</body>
</html>
```